Business Card for Coastal Tundrabridge Advisory

We need a business card for Coastal Tundrabridge Advisory. The company website address is provided below. The company logo is attached. We provide specialized permafrost services to the mining, transportation, and oil & gas industries. The card should be prepared for:
Matthias Korhonen, PhD.
Coastal Tundrabridge Advisory
PO Box 418259
Quillwater, Alaska 99642
Direct: +1-907-555-0143
Email: mkorhonen@tundrabridgeadvisory.example
Website: www.coastaltundrabridgeadvisory.example

```html
<!DOCTYPE html>
<html lang="en">
<head>
<meta charset="utf-8">
<title>Coastal Tundrabridge Advisory – Business Card</title>
<link href="https://fonts.googleapis.com/css2?family=Montserrat:wght@400;500;700&display=swap" rel="stylesheet">
<style>
  :root {
    --ink: #17202b;
    --paper: #ffffff;
    --backdrop: #e6e3de;
    --rule: #17202b;
  }
  * { box-sizing: border-box; margin: 0; padding: 0; }
  html, body { width: 1200px; height: 931px; overflow: hidden; }
  body {
    background: var(--backdrop);
    font-family: "Montserrat", Arial, sans-serif;
    color: var(--ink);
    position: relative;
  }
  .card {
    position: absolute;
    width: 620px;
    height: 354px;
    background: var(--paper);
    border-radius: 22px;
    box-shadow: 0 6px 18px rgba(0,0,0,0.12);
  }
  .card--front { left: 60px; top: 60px; display: flex; align-items: center; justify-content: center; }
  .card--back { left: 520px; top: 517px; }

  .brand-name {
    font-weight: 700;
    color: var(--ink);
    text-transform: uppercase;
    letter-spacing: 0.06em;
    line-height: 1.15;
    text-align: center;
  }
  .card--front .brand-name { font-size: 30px; width: 420px; }
  .card--back .brand-name {
    position: absolute; right: 40px; top: 34px;
    font-size: 19px; width: 300px; text-align: right;
  }
  .rule-top {
    position: absolute; left: 40px; right: 40px; top: 118px;
    height: 2px; background: var(--rule);
  }
  .holder { position: absolute; left: 40px; top: 178px; }
  .holder-name { font-weight: 700; font-size: 25px; }
  .holder-title { font-weight: 400; font-size: 16px; margin-top: 2px; }
  .rule-short {
    position: absolute; left: 40px; top: 244px;
    width: 280px; height: 2px; background: var(--rule);
  }
  .contacts { position: absolute; left: 40px; top: 256px; list-style: none; }
  .contacts li {
    display: flex; align-items: center; gap: 12px;
    font-size: 14px; line-height: 26px;
  }
  .contacts svg { width: 14px; height: 14px; fill: var(--ink); flex: none; }
  .address {
    position: absolute; right: 40px; top: 194px;
    font-size: 14px; line-height: 1.4; text-align: left;
  }
</style>
</head>
<body>
  <section class="card card--front">
    <div class="brand-name">Coastal Tundrabridge Advisory</div>
  </section>

  <section class="card card--back">
    <div class="brand-name">Coastal Tundrabridge Advisory</div>
    <div class="rule-top"></div>
    <div class="holder">
      <div class="holder-name">Matthias Korhonen, PhD.</div>
      <div class="holder-title">Managing Director</div>
    </div>
    <div class="rule-short"></div>
    <ul class="contacts">
      <li>
        <svg viewBox="0 0 24 24" aria-hidden="true"><path d="M6.6 10.8a15.1 15.1 0 0 0 6.6 6.6l2.2-2.2a1 1 0 0 1 1-.25 11.4 11.4 0 0 0 3.6.57 1 1 0 0 1 1 1V20a1 1 0 0 1-1 1A17 17 0 0 1 3 4a1 1 0 0 1 1-1h3.5a1 1 0 0 1 1 1c0 1.25.2 2.45.57 3.57a1 1 0 0 1-.25 1z"/></svg>
        +1-907-555-0143
      </li>
      <li>
        <svg viewBox="0 0 24 24" aria-hidden="true"><path d="M2 5h20v14H2z M2 5l10 8 10-8" /><path d="M3 6l9 7 9-7v12H3z" fill="#fff" opacity="0"/></svg>
        mkorhonen@tundrabridgeadvisory.example
      </li>
      <li>
        <svg viewBox="0 0 24 24" aria-hidden="true"><circle cx="12" cy="12" r="10"/><path d="M2 12h20M12 2c3 3 3 17 0 20M12 2c-3 3-3 17 0 20" stroke="#fff" stroke-width="1.5" fill="none"/></svg>
        www.coastaltundrabridgeadvisory.example
      </li>
    </ul>
    <div class="address">
      PO Box 418259<br>
      Quillwater, Alaska 99642
    </div>
  </section>
</body>
</html>
```